Brintel Works - Fast, Efficient and Gas Mainteance for Domestic, Commercial and Industrial clients

We are in the process of purchasing a new business and would like to get a new logo and business card.
Business is a gas maintenance business that also does new gas installations.
Has been established since 1988.
Services include:
Install all types of gas appliances & equipment inc. hot water units
Maintain / repair / replace all types of gas appliances & equipment

Target Market(s)

Domestic, Commercial and Industrial clients

Industry/Entity Type

Business

Contact Information for Business Card

admin@brintelworks.com.au
07 3918 4726
Brintel Works PTY LTD

Logo Text

Gas Fitting & Plumbing Maintenance Specialists

Font styles to use
Sans Serif

Requirements
Must have
• Logo
• Business name, contact number, email address, web address
• Domestic | Commercial | Industrial Est Since 1988
Nice to have
• Possibly a black card with a flame logo to one side
Should not have
• Spelling errors

```html
<!DOCTYPE html>
<html lang="en">
<head>
<meta charset="utf-8">
<title>Brintel Works – Business Card</title>
<link rel="stylesheet" href="https://fonts.googleapis.com/css2?family=Source+Sans+3:wght@400&display=swap">
<style>
  :root {
    --backdrop: #1e1e1e;
    --card-black: #050505;
    --card-red: #ec2227;
    --card-red-deep: #d41b20;
    --brand-yellow: #f3d812;
    --icon-orange: #f7941d;
    --text-white: #ffffff;
  }
  * { box-sizing: border-box; margin: 0; padding: 0; }
  html, body {
    width: 1200px;
    height: 900px;
    overflow: hidden;
    background: var(--backdrop);
  }
  .stage {
    position: relative;
    width: 1200px;
    height: 900px;
  }
  .card {
    position: absolute;
    top: 184px;
    width: 302px;
    height: 491px;
    border-radius: 12px;
    font-family: "Source Sans 3", sans-serif;
  }
  .card--front {
    left: 299px;
    background: var(--card-black);
    color: var(--text-white);
    text-align: center;
  }
  .card--back {
    left: 646px;
    background: var(--card-red);
  }

  /* Brand lock-up */
  .brand {
    position: absolute;
    top: 112px;
    left: 34px;
    right: 24px;
    display: flex;
    align-items: center;
    gap: 12px;
  }
  .brand-mark {
    width: 40px;
    height: 40px;
    flex: none;
    border-radius: 50%;
    background: var(--card-red);
  }
  .brand-text {
    display: flex;
    flex-direction: column;
    align-items: flex-end;
    color: var(--brand-yellow);
    font-weight: 400;
    line-height: 1;
  }
  .brand-name {
    font-size: 33px;
    letter-spacing: 0.3px;
  }
  .brand-suffix {
    margin-top: 5px;
    font-size: 14px;
    letter-spacing: 2.6px;
  }

  .contact-list {
    position: absolute;
    top: 244px;
    left: 0;
    width: 100%;
    list-style: none;
    font-size: 14px;
    line-height: 18px;
  }
  .contact-item {
    display: flex;
    justify-content: center;
    align-items: center;
    gap: 6px;
  }
  .contact-icon {
    width: 10px;
    height: 10px;
    flex: none;
  }
  .address {
    position: absolute;
    top: 318px;
    left: 0;
    width: 100%;
    font-size: 14px;
    line-height: 18px;
    font-style: normal;
  }
  .sectors {
    position: absolute;
    top: 374px;
    left: 0;
    width: 100%;
    font-size: 14px;
    line-height: 18px;
  }

  /* Back: name set where the large mark stands */
  .back-name {
    position: absolute;
    top: 50%;
    left: 0;
    width: 100%;
    transform: translateY(-50%);
    text-align: center;
    font-size: 36px;
    font-weight: 400;
    color: var(--card-red-deep);
  }
</style>
</head>
<body>
<main class="stage">
  <section class="card card--front" aria-label="Business card front">
    <div class="brand">
      <span class="brand-mark" aria-hidden="true"></span>
      <p class="brand-text">
        <span class="brand-name">Brintel Works</span>
        <span class="brand-suffix">PTY LTD</span>
      </p>
    </div>

    <ul class="contact-list">
      <li class="contact-item">
        <svg class="contact-icon" viewBox="0 0 10 10" aria-hidden="true">
          <path d="M2 0.8 L3.6 2.9 L2.8 3.8 C3.4 5.2 4.8 6.6 6.2 7.2 L7.1 6.4 L9.2 8 L8.2 9.3 C4.6 9.3 0.7 5.4 0.7 1.8 Z" fill="var(--icon-orange)"/>
        </svg>
        <span>07 3918 4726</span>
      </li>
      <li class="contact-item">
        <svg class="contact-icon" viewBox="0 0 10 10" aria-hidden="true">
          <rect x="0.5" y="2" width="9" height="6.5" fill="var(--icon-orange)"/>
          <path d="M0.5 2 L5 5.6 L9.5 2" fill="none" stroke="#050505" stroke-width="0.8"/>
        </svg>
        <span>admin@brintelworks.com.au</span>
      </li>
      <li class="contact-item">
        <svg class="contact-icon" viewBox="0 0 10 10" aria-hidden="true">
          <circle cx="5" cy="5" r="4.5" fill="var(--icon-orange)"/>
          <path d="M0.5 5 H9.5 M5 0.5 V9.5" stroke="#050505" stroke-width="0.7"/>
        </svg>
        <span>www.brintelworks.com.au</span>
      </li>
    </ul>

    <address class="address">
      12345, Address Goes Here<br>
      Country Name, 123456.
    </address>

    <p class="sectors">
      Domestic | Commercial<br>
      Industrial Est Since 1988
    </p>
  </section>

  <section class="card card--back" aria-label="Business card back">
    <p class="back-name">Brintel Works</p>
  </section>
</main>
</body>
</html>
```